Heritage Hollow Business Cards

Require a business card design. <br/><br/>Needs to include logo (either round or long version) plus these details:<br/>Maya Torvell<br/>Heritage Hollow<br/>maya@kelvadtrading.com.au<br/>02 6481 7395<br/>PO Box Glenwarra NSW 2791<br/>www.heritagehollow.com.au<br/><br/>I need in an editable format so that I can create for multiple staff members. <br/><br/>

Target Market(s)

We are an online store selling renovation products to home owners are builders. Looking for a classic classy design.

Industry/Entity Type

Home And Garden

Contact Information for Business Card

Maya Torvell
Heritage Hollow
maya@kelvadtrading.com.au
02 6481 7395
PO Box Glenwarra NSW 2791
www.heritagehollow.com.au

Colors

Designer to choose colors to be used in the design.

Requirements
Must have
• Must include Logo.

```html
<!DOCTYPE html>
<html lang="en">
<head>
<meta charset="utf-8">
<title>Heritage Hollow Business Cards</title>
<link rel="stylesheet" href="https://fonts.googleapis.com/css2?family=Josefin+Sans:wght@300&family=Source+Sans+3:wght@400&display=swap">
<style>
  :root {
    --backdrop: #c1c1c1;
    --paper: #f8f8f8;
    --paper-back: #ffffff;
    --ink: #121418;
    --charcoal: #262626;
    --sage: #516d5f;
    --light: #ffffff;
  }
  * { margin: 0; padding: 0; box-sizing: border-box; }
  html, body { width: 962px; height: 1200px; overflow: hidden; background: var(--backdrop); }
  body { position: relative; font-family: "Source Sans 3", sans-serif; }

  .card { position: absolute; width: 521px; height: 297px; overflow: hidden; }

  /* Front */
  .card-front { left: 235px; top: 191px; background: var(--paper); }
  .front-panel { position: absolute; left: 260px; top: 0; width: 261px; height: 297px; background: var(--ink); }
  .brand-mark {
    position: absolute; left: 39px; top: 52px; width: 186px; height: 186px;
    border: 1px solid var(--ink); border-radius: 50%;
    display: flex; align-items: center; justify-content: center; text-align: center;
    font-size: 27px; line-height: 1.05; color: var(--ink);
  }
  .contact-rail {
    position: absolute; left: 245px; top: 101px; width: 31px; height: 196px;
    background: var(--sage); border-radius: 16px;
  }
  .contact-icon { position: absolute; left: 5px; width: 21px; height: 21px; fill: var(--light); }
  .person-name {
    position: absolute; left: 292px; top: 33px; width: 215px;
    font-family: "Josefin Sans", sans-serif; font-weight: 300; font-size: 25px; line-height: 1;
    letter-spacing: 0.5px; color: var(--light); white-space: nowrap;
  }
  .person-role { position: absolute; left: 292px; top: 65px; font-size: 16px; line-height: 1.2; color: var(--light); }
  .contact-list { list-style: none; }
  .contact-item {
    position: absolute; left: 301px; font-size: 12px; line-height: 1.2; color: var(--light); white-space: nowrap;
    transform: translateY(-50%);
  }

  /* Back */
  .card-back { left: 232px; top: 583px; background: var(--paper-back); }
  .back-wordmark {
    position: absolute; left: 0; right: 0; top: 104px; text-align: center;
    font-size: 42px; line-height: 1.2; color: var(--ink);
  }
  .back-band {
    position: absolute; left: 0; top: 176px; width: 521px; height: 48px;
    background: var(--sage); border-radius: 26px 44px 0 0;
  }
  .back-footer {
    position: absolute; left: 0; top: 224px; width: 521px; height: 73px;
    background: var(--charcoal); display: flex; align-items: center; justify-content: center;
    color: var(--light); font-size: 12.5px; letter-spacing: 2.6px;
  }
</style>
</head>
<body>

<section class="card card-front" aria-label="Business card front">
  <div class="brand-mark">Heritage<br>Hollow</div>
  <div class="front-panel"></div>

  <div class="contact-rail">
    <svg class="contact-icon" style="top:22px" viewBox="0 0 24 24" aria-hidden="true">
      <path d="M6.6 10.8a15.1 15.1 0 0 0 6.6 6.6l2.2-2.2a1 1 0 0 1 1-.25 11.4 11.4 0 0 0 3.6.57 1 1 0 0 1 1 1V20a1 1 0 0 1-1 1A17 17 0 0 1 3 4a1 1 0 0 1 1-1h3.5a1 1 0 0 1 1 1c0 1.25.2 2.45.57 3.57a1 1 0 0 1-.25 1z"/>
    </svg>
    <svg class="contact-icon" style="top:62px" viewBox="0 0 24 24" aria-hidden="true">
      <path d="M2 5h20v14H2z M3.5 6.5l8.5 7 8.5-7 M3.5 17.5l6-5.5 M20.5 17.5l-6-5.5" fill="none" stroke="#fff" stroke-width="1.4"/>
    </svg>
    <svg class="contact-icon" style="top:105px" viewBox="0 0 24 24" aria-hidden="true">
      <circle cx="12" cy="12" r="10"/>
      <path d="M7 6c2 0 3 1 3 2.5S8 10 8 12s2 2 2 4-1 3-1 3M15 5c-1 1-1 2.5 .5 3s2.5 1 2 3-2 2-1.5 4" fill="none" stroke="#516d5f" stroke-width="1.6"/>
    </svg>
    <svg class="contact-icon" style="top:148px" viewBox="0 0 24 24" aria-hidden="true">
      <path d="M12 1.5a7.5 7.5 0 0 0-7.5 7.5c0 5.6 7.5 13.5 7.5 13.5S19.5 14.6 19.5 9A7.5 7.5 0 0 0 12 1.5zm0 10.3a2.8 2.8 0 1 1 0-5.6 2.8 2.8 0 0 1 0 5.6z"/>
    </svg>
  </div>

  <h1 class="person-name">MAYA TORVELL</h1>
  <p class="person-role">Director</p>
  <ul class="contact-list">
    <li class="contact-item" style="top:134px">02 6481 7395</li>
    <li class="contact-item" style="top:173px">maya@kelvadtrading.com.au</li>
    <li class="contact-item" style="top:216px">www.heritagehollow.com.au</li>
    <li class="contact-item" style="top:260px">PO Box Glenwarra NSW 2791</li>
  </ul>
</section>

<section class="card card-back" aria-label="Business card back">
  <div class="back-wordmark">Heritage Hollow</div>
  <div class="back-band"></div>
  <div class="back-footer">www.heritagehollow.com.au</div>
</section>

</body>
</html>
```